yourCartly - a stylish trolley for apartments

We neede a simple website to sell our Trolley, for apartment use.
The colour theme is red, blask & white. Our logo is attached and this needs to be on the Home page.
The website only needs a Home Page plus 4 other pges.
In the attachment you will find a site map.

You can check out the following two sites to see what I like:
www.plainvexo.com/design-showcase-inspiration/minimalist-portfolio-website/
www.brightquillor.com/inspiration/40-beautiful-web-design-portfolios/ in this site especially
Dario Penhaske
G K Maker
Nine 17 Works
Marcus Bell

And especially Lamp - I ike the simpicity of the site esp as we are only selling one product

Target Market(s)

Apartment dwellers

Industry/Entity Type

Apartment

Requirements
Must have
• This website must have 4 pages.
We need Zorva, Pelicoin and Quidnet portals.
Order Form for Trolley
Payment form.

```html
<!DOCTYPE html>
<html lang="en">
<head>
<meta charset="utf-8">
<title>yourCartly – Home</title>
<link href="https://fonts.googleapis.com/css2?family=PT+Sans:ital,wght@0,400;0,700;1,400&display=swap" rel="stylesheet">
<style>
:root{
  --red:#b01818;
  --ink:#333;
  --text:#555;
  --muted:#777;
  --head-bg:#f1f1f1;
  --panel:#f0f0f0;
  --line:#c8c8c8;
  --nav-top:#4a4a4a;
  --nav-bot:#1c1c1c;
  --footer:#262626;
  --footer-text:#e6e6e6;
  --accent:#f2d23a;
  --white:#fff;
}
*{box-sizing:border-box;margin:0;padding:0}
html,body{width:781px;height:1200px;overflow:hidden;background:var(--white)}
body{position:relative;font-family:"PT Sans",Arial,sans-serif;color:var(--text)}
.abs{position:absolute}
.site-header{position:absolute;left:0;top:0;width:781px;height:141px;background:var(--head-bg)}
.brand{left:88px;top:84px;display:flex;align-items:center;gap:8px}
.brand-mark{width:16px;height:16px;background:var(--red)}
.brand-name{font-size:22px;font-weight:700;color:var(--ink)}
.account-links{left:395px;top:12px;font-size:9px;color:var(--ink)}
.search{left:502px;top:7px;width:187px;height:21px;border:1px solid var(--line);background:var(--white);display:flex}
.search span{flex:1;font-size:9px;font-style:italic;color:var(--muted);padding:4px 7px}
.search b{width:39px;background:linear-gradient(#f6f6f6,#d9d9d9);display:flex;align-items:center;justify-content:center;border-left:1px solid var(--line)}
.phone{left:494px;top:40px;display:flex;align-items:center;gap:12px;font-size:22px;color:var(--ink)}
.pay-portals{left:508px;top:93px;display:flex;gap:5px}
.pay-portals span{font-size:9px;font-weight:700;color:var(--ink);background:var(--white);border:1px solid var(--line);border-radius:3px;padding:3px 5px}
.main-nav{left:85px;top:127px;width:611px;height:33px;background:linear-gradient(var(--nav-top),var(--nav-bot));display:flex}
.main-nav a{flex:1;text-align:center;line-height:33px;font-size:11px;color:var(--white);text-decoration:none}
.main-nav a.current{color:var(--accent);background:#111}
.slider{left:85px;top:167px;width:611px;height:357px;border:1px solid var(--line);background:#f7f7f7;box-shadow:0 8px 10px -8px rgba(0,0,0,.35)}
.slide-photo{left:18px;top:12px;width:573px;height:332px;background:linear-gradient(90deg,#6f6f6f,#d9d9d9 30%,#9a9a9a 55%,#e0e0e0 80%,#8a8a8a),#999}
.slide-photo::after{content:"";position:absolute;left:0;right:0;bottom:0;height:110px;background:linear-gradient(#2a2a2a,#111)}
.slider-arrow{top:157px}
h2{font-weight:400;color:var(--ink)}
h2 .cap{color:var(--red)}
.welcome{left:96px;top:540px;width:276px}
.welcome h2{font-size:12px}
.welcome p{font-size:8.6px;line-height:19.4px;margin-top:1px}
.red{color:var(--red)}
.more{font-size:8.6px;font-weight:700;font-style:italic;color:var(--red);text-decoration:none}
.welcome .read{position:absolute;left:187px;top:157px}
.welcome-photo{left:374px;top:552px;width:152px;height:154px;background:linear-gradient(160deg,#f4f4f4,#c9c9c9 60%,#5a5a5a)}
.products{left:85px;top:727px;width:455px;height:241px;background:var(--panel)}
.products h2{position:absolute;left:12px;top:5px;font-size:16px}
.product{position:absolute;top:42px;width:170px;text-align:center}
.product h3{font-size:13px;font-weight:400;color:var(--ink);text-align:left;margin-left:0}
.product-img{width:157px;height:81px;margin:8px 0 0 1px;border:1px solid #444;background:var(--white);display:flex;align-items:center;justify-content:center}
.product-img i{display:block;width:110px;height:50px;background:linear-gradient(#444,#aaa);border-radius:4px}
.product p{font-size:8.6px;line-height:19.4px;margin-top:10px;color:var(--ink)}
.product a{font-size:8.6px;color:var(--red);text-decoration:none;display:block;line-height:18px;margin-left:20px}
.quality{left:559px;top:540px;width:130px}
.quality h2{font-size:12px}
.quality ul{list-style:none;margin-top:1px}
.quality li{font-size:8.5px;line-height:19.4px;color:var(--ink)}
.quality li svg{vertical-align:-3px;margin-right:6px}
.testimonials h2{font-size:16px;margin-top:14px}
.testimonials blockquote{font-size:9.4px;font-style:italic;line-height:19.4px;margin-top:16px;color:var(--text)}
.testimonials cite{font-size:8.3px;margin-left:20px;color:var(--ink)}
.site-footer{left:0;top:980px;width:781px;height:220px;background:var(--footer);color:var(--footer-text)}
.order h2{position:absolute;left:97px;top:10px;font-size:13px;color:var(--white)}
.field{position:absolute;height:21px;background:var(--white);font-size:8px;font-style:italic;color:var(--muted);padding:5px 10px}
.drop{position:absolute;right:0;top:0;width:38px;height:21px;background:linear-gradient(#eee,#bbb);display:flex;align-items:center;justify-content:center}
.btn{position:absolute;top:181px;width:70px;height:20px;background:linear-gradient(#fff,#cfcfcf);color:var(--ink);font-size:10px;text-align:center;line-height:20px}
.footer-nav a{position:absolute;left:370px;font-size:10px;color:var(--white);text-decoration:none}
.contact{position:absolute;left:522px;top:12px;font-size:10px;line-height:19.4px;color:var(--white)}
.contact h2{font-size:15px;color:var(--white);margin-bottom:16px}
.contact small{font-size:8.4px}
</style>
</head>
<body>

<header class="site-header">
  <div class="abs brand"><span class="brand-mark"></span><span class="brand-name">yourCartly</span></div>
  <div class="abs account-links">Create an account &nbsp;|&nbsp; Login</div>
  <div class="abs search"><span>Search</span><b><svg width="16" height="16" viewBox="0 0 16 16"><circle cx="6.5" cy="6.5" r="4.5" fill="none" stroke="#333" stroke-width="2"/><path d="M10 10l5 5" stroke="#333" stroke-width="2.5"/></svg></b></div>
  <div class="abs phone">
    <svg width="34" height="24" viewBox="0 0 34 24"><path d="M2 8c0-5 30-5 30 0v3h-8V8H10v3H2z" fill="var(--red)"/><path d="M7 12h20l3 11H4z" fill="var(--red)"/><circle cx="17" cy="17" r="3.5" fill="#fff"/></svg>
    <span>+1390 7214 38</span>
  </div>
  <div class="abs pay-portals"><span>Gavrel</span><span>Quidnet</span><span>Pelicoin</span><span>Zorva</span></div>
</header>

<nav class="abs main-nav">
  <a class="current" href="#">Home</a><a href="#">yourCartly</a><a href="#">Gallery</a><a href="#">Shopping Cart</a><a href="#">Payment</a><a href="#">Contact Us</a>
</nav>

<section class="abs slider">
  <div class="abs slide-photo" role="img" aria-label="Chrome luggage trolley loaded with suitcases beside steel lift doors"></div>
  <svg class="abs slider-arrow" style="left:32px" width="48" height="48" viewBox="0 0 48 48"><circle cx="24" cy="24" r="22" fill="rgba(255,255,255,.2)" stroke="#e8e8e8" stroke-width="2"/><path d="M30 13L14 24l16 11z" fill="#e8e8e8"/></svg>
  <svg class="abs slider-arrow" style="left:533px" width="48" height="48" viewBox="0 0 48 48"><circle cx="24" cy="24" r="22" fill="rgba(255,255,255,.2)" stroke="#e8e8e8" stroke-width="2"/><path d="M18 13l16 11-16 11z" fill="#e8e8e8"/></svg>
</section>

<section class="abs welcome">
  <h2><span class="cap">W</span>el-come to <span class="red">your</span>Cartly</h2>
  <p><span class="red">your</span>Cartly evolved from demand!&nbsp; Apartment dwellers everywhere are<br>calling for a solution to moving shopping, luggage and other goods<br>from car to apartment, and vice versa. Other trolleys on the market are<br>not versatile, they are not robust, but more importantly, they are NOT<br>stylish! The emphasis of yourCartly is on style. This trolley is stylish<br>enough to remain in your apartment as a piece of furniture. It features<br>a versatile flat-bed and hanger, to cope with all your transport needs.</p>
  <a class="more read" href="#">Read more...</a>
</section>
<div class="abs welcome-photo" role="img" aria-label="Parent pushing a red flat-bed trolley carrying a baby seat, child alongside"></div>

<section class="abs products">
  <h2><span class="cap">O</span>ur products</h2>
  <svg class="abs" style="left:358px;top:6px" width="80" height="26" viewBox="0 0 80 26"><circle cx="13" cy="13" r="11.5" fill="#fff" stroke="#333" stroke-width="1.5"/><path d="M16 7l-7 6 7 6z" fill="#333"/><circle cx="46" cy="13" r="11.5" fill="#fff" stroke="#333" stroke-width="1.5"/><path d="M43 7l7 6-7 6z" fill="#333"/></svg>
  <div class="product" style="left:39px">
    <h3>Robust &amp; Options</h3>
    <div class="product-img"><i role="img" aria-label="Round steel display trolley"></i></div>
    <p>All products have a range of accesso-<br>ries and options enhancing their<br>effectiveness in your retail situation.</p>
    <a href="#">More Parts &amp; Options</a>
  </div>
  <div class="product" style="left:260px">
    <h3>Long Retail Barrow</h3>
    <div class="product-img"><i role="img" aria-label="Long black retail barrow on green frame"></i></div>
    <p>All products have a range of accesso-<br>ries and options enhancing their<br>effectiveness in your retail situation.</p>
    <a href="#">More Parts &amp; Options</a>
  </div>
</section>

<aside class="abs quality">
  <h2>Our product quality</h2>
  <ul>
    <li><svg width="16" height="13" viewBox="0 0 16 13"><rect x="1" y="3" width="9" height="9" fill="none" stroke="#999"/><path d="M2 7l3 3 9-9" fill="none" stroke="var(--red)" stroke-width="2.5"/></svg>Bottom up watering &amp; low<br>footprint vs. volume of display.</li>
    <li><svg width="16" height="13" viewBox="0 0 16 13"><rect x="1" y="3" width="9" height="9" fill="none" stroke="#999"/><path d="M2 7l3 3 9-9" fill="none" stroke="var(--red)" stroke-width="2.5"/></svg>Flexibility and mobility<br>with multiple applications.</li>
    <li><svg width="16" height="13" viewBox="0 0 16 13"><rect x="1" y="3" width="9" height="9" fill="none" stroke="#999"/><path d="M2 7l3 3 9-9" fill="none" stroke="var(--red)" stroke-width="2.5"/></svg>Proven in the international<br>environment to do a better job<br>than any alternative product.</li>
    <li><svg width="16" height="13" viewBox="0 0 16 13"><rect x="1" y="3" width="9" height="9" fill="none" stroke="#999"/><path d="M2 7l3 3 9-9" fill="none" stroke="var(--red)" stroke-width="2.5"/></svg>Displays at their best in<br>blocks of colour &amp; texture for the<br>wow factor.</li>
    <li><svg width="16" height="13" viewBox="0 0 16 13"><rect x="1" y="3" width="9" height="9" fill="none" stroke="#999"/><path d="M2 7l3 3 9-9" fill="none" stroke="var(--red)" stroke-width="2.5"/></svg>Simple clean design to<br>meet industry needs &amp; to look<br>great.</li>
  </ul>
  <div class="testimonials">
    <h2><span class="cap">T</span>estimonials</h2>
    <blockquote>"A big step forward in trolley<br>design. Offers a strong buying<br>incentive for customers: conve-<br>nience." <cite>Tom Haskel</cite></blockquote>
    <p style="margin:1px 0 0 70px"><a class="more" href="#">Read more...</a></p>
  </div>
</aside>

<footer class="abs site-footer">
  <div class="order">
    <h2>Order Now!</h2>
    <div class="field" style="left:97px;top:36px;width:183px">Name</div>
    <div class="field" style="left:97px;top:73px;width:183px">E-mail address</div>
    <div class="field" style="left:97px;top:111px;width:131px">Select trolley name<span class="drop"><svg width="14" height="14" viewBox="0 0 14 14"><circle cx="7" cy="7" r="6" fill="#ddd" stroke="#333"/><path d="M4 5h6l-3 5z" fill="#333"/></svg></span></div>
    <div class="field" style="left:240px;top:111px;width:41px;padding-left:6px">1<span class="drop" style="width:20px"><svg width="14" height="14" viewBox="0 0 14 14"><circle cx="7" cy="7" r="6" fill="#ddd" stroke="#333"/><path d="M4 5h6l-3 5z" fill="#333"/></svg></span></div>
    <div class="field" style="left:97px;top:147px;width:183px">Contact no.</div>
    <div class="btn" style="left:109px">Send</div>
    <div class="btn" style="left:196px">Reset</div>
  </div>
  <nav class="footer-nav">
    <a href="#" style="top:35px">Home</a>
    <a href="#" style="top:61px">yourCartly</a>
    <a href="#" style="top:87px">Gallery</a>
    <a href="#" style="top:120px">Shopping Cart</a>
    <a href="#" style="top:153px">Payment</a>
    <a href="#" style="top:185px">Contact Us</a>
  </nav>
  <div class="contact">
    <h2><span class="red">your</span>Cartly</h2>
    Main: <small>+64 6 555 0142</small><br>
    Fax: &nbsp;<small>+64 6 555 0197</small><br>
    Email: <small>info@yourcartly.com</small><br>
    Address: <small>14 Ferncliff Lane,The emphasis of<br>yourCartly is on style.</small>
  </div>
</footer>

</body>
</html>
```